MRT Property - Business Cards

Looking for a business card & general letterhead, signage etc design for our new logo.

Colours:
000a20
0056a2
00b5ef
0088ce
68cef2

Fonts:
Poppins
Karla

Please keep look and feel of new brand - example in the zip package I sent.

```html
<!DOCTYPE html>
<html lang="en">
<head>
<meta charset="utf-8">
<title>MRT Property – Business Cards</title>
<link rel="stylesheet" href="https://fonts.googleapis.com/css2?family=Poppins:wght@300;400;500;700&family=Karla:wght@400;500&display=swap">
<style>
  :root {
    --ink: #000a20;
    --brand-blue: #0056a2;
    --sky: #00b5ef;
    --mid-blue: #0088ce;
    --pale-blue: #68cef2;
    --paper: #ffffff;
    --stage: #1d1e22;
    --text-dark: #1a1a1a;
  }
  * { box-sizing: border-box; margin: 0; padding: 0; }
  html, body {
    width: 1200px; height: 900px; overflow: hidden;
    background: var(--stage);
  }
  .sheet {
    position: relative; width: 1200px; height: 900px;
    display: flex; flex-direction: column; align-items: center; justify-content: center;
    gap: 50px;
  }
  .card {
    position: relative; width: 600px; height: 343px;
    border-radius: 22px; overflow: hidden;
    box-shadow: 0 18px 40px rgba(0,0,0,.45);
  }

  /* Front */
  .card--front { background: var(--brand-blue); }
  .card--front .wordmark {
    position: absolute; right: 48px; top: 140px;
    font-family: "Poppins", sans-serif; font-weight: 700;
    font-size: 46px; letter-spacing: 1px; color: var(--paper);
  }

  /* Back */
  .card--back { background: var(--paper); }
  .brand {
    position: absolute; left: 64px; top: 52px;
    display: flex; align-items: center; gap: 16px;
  }
  .brand__dot {
    width: 40px; height: 40px; border-radius: 50%;
    background: var(--mid-blue);
  }
  .brand__name {
    font-family: "Poppins", sans-serif; font-weight: 700;
    font-size: 44px; letter-spacing: 1px; color: var(--brand-blue);
  }
  .details {
    position: absolute; left: 64px; top: 150px;
    display: flex; align-items: center; gap: 22px;
  }
  .person__name {
    font-family: "Poppins", sans-serif; font-weight: 300;
    font-size: 30px; color: var(--brand-blue); line-height: 1.1;
  }
  .person__role {
    font-family: "Karla", sans-serif; font-weight: 500;
    font-size: 15px; color: var(--text-dark); margin-top: 4px;
  }
  .divider { width: 1.5px; height: 76px; background: var(--brand-blue); }
  .contacts { list-style: none; display: flex; flex-direction: column; gap: 8px; }
  .contacts li {
    display: flex; align-items: center; gap: 10px;
    font-family: "Karla", sans-serif; font-size: 15px; color: var(--text-dark);
  }
  .contacts svg { width: 14px; height: 14px; flex: none; }
  .address-band {
    position: absolute; left: 0; right: 0; bottom: 22px; height: 46px;
    background: var(--brand-blue);
    display: flex; align-items: center; justify-content: center;
    font-family: "Poppins", sans-serif; font-weight: 400;
    font-size: 15px; color: var(--paper); letter-spacing: .3px;
  }
</style>
</head>
<body>
<main class="sheet">
  <section class="card card--front" aria-label="Business card front">
    <div class="wordmark">MRT Property</div>
  </section>

  <section class="card card--back" aria-label="Business card back">
    <div class="brand">
      <span class="brand__dot"></span>
      <span class="brand__name">MRT Property</span>
    </div>

    <div class="details">
      <div class="person">
        <div class="person__name">Daniel Reyes</div>
        <div class="person__role">Managing Director</div>
      </div>
      <div class="divider"></div>
      <ul class="contacts">
        <li>
          <svg viewBox="0 0 16 16" aria-hidden="true"><path fill="var(--brand-blue)" d="M3.6 1.5l2.3 2.6-1.3 1.7c.9 2 2.6 3.7 4.6 4.6l1.7-1.3 2.6 2.3-1.4 2.1C6.9 15.2.8 9.1 1.5 3z"/></svg>
          1 (555) 014-2290
        </li>
        <li>
          <svg viewBox="0 0 16 16" aria-hidden="true"><rect x="1" y="3" width="14" height="10" rx="1.5" fill="var(--brand-blue)"/><path d="M1.5 4l6.5 5 6.5-5" stroke="#fff" stroke-width="1.3" fill="none"/></svg>
          info@mrtproperty.com
        </li>
        <li>
          <svg viewBox="0 0 16 16" aria-hidden="true"><circle cx="8" cy="8" r="7" fill="var(--brand-blue)"/><path d="M1 8h14M8 1c-3 3.5-3 10.5 0 14M8 1c3 3.5 3 10.5 0 14" stroke="#fff" stroke-width="1" fill="none"/></svg>
          www.mrtproperty.com
        </li>
      </ul>
    </div>

    <div class="address-band">418 Maple Ridge Ave Suite 210 Dayton Ohio 45402</div>
  </section>
</main>
</body>
</html>
```